1" x 3" label needed for essential oil bottle(s) - new ecommerce company

We need a label designed for 10 ml bottles of essential oils. We are offering 9 different types of essential oil: Lavender, Cedarwood, Eucalyptus, Frankincense, Lemon, Orange, Peppermint, Rosemary, and Tea Tree. The label should have a space for the type of essential oil. The bottles are an amber color (am including a photo) as essential oils are sensitive to light. also am including an AI file of our logo, which we'd like included on the label; the logo file also contains our logo colors, a dark blue and light grey. We'd also like the following on the label: "CAUTION: EYE AND SKIN IRRITANT. Avoid contact with eyes and skin. Wash hands after handling. If eye contact occurs, flush with water for 15 minutes. Not intended for topical or internal use. Contains Essential Oils. KEEP OUT OF REACH OF CHILDREN."
Also "Ingredients: 100% pure essential oil, GC tested."
Also "0.33 fl oz (10 ml)
Finally, we will need to include a sideways bar code on the right side of the label, so need 3/8" of white space on the right of the label.
We'd like the label to be calming, but modern, friendly, and confident.

```html
<!DOCTYPE html>
<html lang="en">
<head>
<meta charset="UTF-8">
<title>Essential Oil Labels</title>
<link href="https://fonts.googleapis.com/css2?family=Jost:wght@400;500;600&display=swap" rel="stylesheet">
<style>
  :root {
    --canvas-bg: #f1f1f1;
    --cedarwood: #b5623e;
    --eucalyptus: #48525e;
    --rosemary: #c09d91;
    --ink-light: #f4efea;
    --mark-cedar: #d49a7c;
    --mark-euca: #6d7884;
    --mark-rose: #d7bdb3;
    --barcode-zone: #ffffff;
  }
  * { margin: 0; padding: 0; box-sizing: border-box; }
  html, body { width: 1200px; height: 900px; overflow: hidden; }
  body {
    background: var(--canvas-bg);
    font-family: "Jost", sans-serif;
    display: flex;
    flex-direction: column;
    align-items: center;
    justify-content: center;
    gap: 20px;
  }

  /* 3in x 1in wrap label at 260px per inch */
  .label {
    display: grid;
    grid-template-columns: 390px 292px 98px;
    width: 780px;
    height: 260px;
    color: var(--ink-light);
  }
  .label--cedarwood { background: var(--cedarwood); --mark: var(--mark-cedar); }
  .label--eucalyptus { background: var(--eucalyptus); --mark: var(--mark-euca); }
  .label--rosemary { background: var(--rosemary); --mark: var(--mark-rose); }

  /* back panel: safety + ingredients */
  .info-panel {
    display: flex;
    flex-direction: column;
    justify-content: center;
    gap: 9px;
    padding: 0 22px 0 24px;
    font-size: 10.5px;
    line-height: 1.45;
    letter-spacing: 0.2px;
  }
  .info-panel strong { font-weight: 600; letter-spacing: 0.6px; }
  .info-panel__volume { font-weight: 500; }

  /* front panel */
  .front-panel {
    position: relative;
    text-align: center;
  }
  .brand-vertical {
    position: absolute;
    left: 0;
    top: 30px;
    height: 200px;
    width: 28px;
    writing-mode: vertical-rl;
    transform: rotate(180deg);
    font-size: 21px;
    letter-spacing: 6px;
    line-height: 28px;
    text-align: center;
  }
  .brand-mark {
    position: absolute;
    left: 28px;
    right: 0;
    top: 44px;
    display: flex;
    flex-direction: column;
    align-items: center;
    gap: 8px;
    color: var(--mark);
  }
  .brand-mark__dot {
    width: 12px;
    height: 12px;
    border-radius: 50%;
    background: var(--mark);
  }
  .brand-mark__name {
    font-size: 14px;
    letter-spacing: 3.5px;
  }
  .oil-name {
    position: absolute;
    left: 28px;
    right: 0;
    top: 160px;
    font-size: 13px;
    font-weight: 500;
    letter-spacing: 3px;
  }
  .oil-tagline {
    position: absolute;
    left: 28px;
    right: 0;
    top: 184px;
    font-size: 12px;
    letter-spacing: 2.2px;
  }
  .oil-volume {
    position: absolute;
    left: 28px;
    right: 0;
    top: 212px;
    font-size: 11px;
    font-weight: 500;
  }

  /* 3/8in clear zone for the sideways barcode */
  .barcode-zone { background: var(--barcode-zone); }
</style>
</head>
<body>
  <section class="label label--cedarwood">
    <div class="info-panel">
      <p><strong>CAUTION: EYE AND SKIN IRRITANT.</strong> Avoid contact with eyes and skin. Wash hands after handling. If eye contact occurs, flush with water for 15 minutes. Not intended for topical or internal use. Contains Essential Oils.</p>
      <p><strong>KEEP OUT OF REACH OF CHILDREN.</strong></p>
      <p>Ingredients: 100% pure essential oil, GC tested.</p>
      <p class="info-panel__volume">0.33 fl oz (10 ml)</p>
    </div>
    <div class="front-panel">
      <div class="brand-vertical">SOLVERA</div>
      <div class="brand-mark"><span class="brand-mark__dot"></span><span class="brand-mark__name">SOLVERA</span></div>
      <h2 class="oil-name">CEDARWOOD</h2>
      <p class="oil-tagline">100% Pure Essential Oil</p>
      <p class="oil-volume">10ml ℮0.33fl.oz.</p>
    </div>
    <div class="barcode-zone"></div>
  </section>

  <section class="label label--eucalyptus">
    <div class="info-panel">
      <p><strong>CAUTION: EYE AND SKIN IRRITANT.</strong> Avoid contact with eyes and skin. Wash hands after handling. If eye contact occurs, flush with water for 15 minutes. Not intended for topical or internal use. Contains Essential Oils.</p>
      <p><strong>KEEP OUT OF REACH OF CHILDREN.</strong></p>
      <p>Ingredients: 100% pure essential oil, GC tested.</p>
      <p class="info-panel__volume">0.33 fl oz (10 ml)</p>
    </div>
    <div class="front-panel">
      <div class="brand-vertical">SOLVERA</div>
      <div class="brand-mark"><span class="brand-mark__dot"></span><span class="brand-mark__name">SOLVERA</span></div>
      <h2 class="oil-name">EUCALYPTUS</h2>
      <p class="oil-tagline">100% Pure Essential Oil</p>
      <p class="oil-volume">10ml ℮0.33fl.oz.</p>
    </div>
    <div class="barcode-zone"></div>
  </section>

  <section class="label label--rosemary">
    <div class="info-panel">
      <p><strong>CAUTION: EYE AND SKIN IRRITANT.</strong> Avoid contact with eyes and skin. Wash hands after handling. If eye contact occurs, flush with water for 15 minutes. Not intended for topical or internal use. Contains Essential Oils.</p>
      <p><strong>KEEP OUT OF REACH OF CHILDREN.</strong></p>
      <p>Ingredients: 100% pure essential oil, GC tested.</p>
      <p class="info-panel__volume">0.33 fl oz (10 ml)</p>
    </div>
    <div class="front-panel">
      <div class="brand-vertical">SOLVERA</div>
      <div class="brand-mark"><span class="brand-mark__dot"></span><span class="brand-mark__name">SOLVERA</span></div>
      <h2 class="oil-name">ROSEMARY</h2>
      <p class="oil-tagline">100% Pure Essential Oil</p>
      <p class="oil-volume">10ml ℮0.33fl.oz.</p>
    </div>
    <div class="barcode-zone"></div>
  </section>
</body>
</html>
```